Velk Partners Building Business Cards

We need a business card that reflects our business as "Solar Experts" in San Diego. Browse our website www.velkpartners.example our License needs to be displayed as "CSLB# 3867140" our phone number is (619) 555-0187

Save thousands on your electric bills and increase the value of your home while helping to protect the environment. Our solar installation experts will help you design the system that's right for you, using only the highest quality equipment that will look great and give you ideal performance. Our goal is to make you energy independent, and get your electric bill to 0.

Paul Osterby
(619) 555-0187
paul@velkpartners.example

Target Market(s)

Home owners in san diego looking for solar

Industry/Entity Type

Solar Energy

Contact Information for Business Card

Paul Osterby
(619) 555-0187
paul@velkpartners.example

Font styles to use
Other font styles liked:
• Use our logo font

Requirements
Must have
• License needs to be displayed as "CSLB# 3867140" our phone number is (619) 555-0187
Nice to have
• Real images of rooftop home solar in san diego
Should not have
• our business address

```html
<!DOCTYPE html>
<html lang="en">
<head>
<meta charset="utf-8">
<title>Velk Partners Building Business Cards</title>
<link rel="stylesheet" href="https://fonts.googleapis.com/css2?family=Open+Sans:wght@400;600;800&display=swap">
<style>
  :root {
    --navy: #1a3a73;
    --sun: #f6ab00;
    --white: #ffffff;
    --stage: #e9eced;
    --ink-soft: #dfe6f2;
  }
  * { box-sizing: border-box; margin: 0; padding: 0; }
  html, body { width: 1200px; height: 812px; overflow: hidden; }
  body {
    background: var(--stage);
    font-family: "Open Sans", sans-serif;
    display: flex;
    align-items: center;
    justify-content: center;
    gap: 40px;
  }
  .card {
    position: relative;
    width: 540px;
    height: 309px;
    overflow: hidden;
    box-shadow: 0 6px 18px rgba(0,0,0,0.18);
  }
  /* Back side */
  .card-back {
    background: var(--navy);
    display: flex;
    flex-direction: column;
    align-items: center;
    justify-content: center;
    gap: 26px;
  }
  .brand-back {
    display: flex;
    align-items: center;
    gap: 14px;
    color: var(--sun);
    font-weight: 800;
    font-size: 30px;
  }
  .brand-dot {
    width: 42px; height: 42px;
    border-radius: 50%;
    background: var(--sun);
  }
  .back-url {
    color: var(--ink-soft);
    font-size: 15px;
    letter-spacing: 3px;
    text-transform: uppercase;
  }
  /* Front side */
  .card-front { background: var(--white); }
  .front-shapes { position: absolute; inset: 0; }
  .brand-front {
    position: absolute;
    left: 34px;
    top: 128px;
    color: var(--navy);
    font-weight: 800;
    font-size: 25px;
    line-height: 1.1;
    width: 220px;
  }
  .contact {
    position: absolute;
    right: 24px;
    top: 78px;
    text-align: right;
    color: var(--white);
    font-size: 13px;
    line-height: 1.55;
  }
  .contact-name { color: var(--sun); font-weight: 800; font-size: 19px; line-height: 1.3; }
  .contact-row { display: flex; align-items: center; justify-content: flex-end; gap: 7px; }
  .contact-icon { width: 13px; height: 13px; flex: none; }
  .contact-gap { margin-top: 10px; }
</style>
</head>
<body>
  <section class="card card-back">
    <div class="brand-back"><span class="brand-dot"></span>Velk Partners Building</div>
    <p class="back-url">www.velkpartners.example</p>
  </section>

  <section class="card card-front">
    <svg class="front-shapes" viewBox="0 0 540 309" width="540" height="309" aria-hidden="true">
      <polygon fill="var(--sun)" points="390,0 412,0 246,291 150,309 124,309 228,283"/>
      <polygon fill="var(--navy)" points="418,0 540,0 540,309 160,309 252,292"/>
    </svg>
    <p class="brand-front">Velk Partners Building</p>
    <div class="contact">
      <p class="contact-name">Paul Osterby</p>
      <p>CEO/Founder</p>
      <p>CSLB# 3867140</p>
      <p class="contact-row contact-gap">(619) 555-0187
        <svg class="contact-icon" viewBox="0 0 16 16"><path fill="var(--sun)" d="M3.6 1.2l2.3 2.6-1.4 1.9c.9 2.1 2.6 3.9 4.8 4.8l1.9-1.4 2.6 2.3-1.6 2.6C6.8 13.6 2.4 9.2 1 3.8z"/></svg>
      </p>
      <p class="contact-row">paul@velkpartners.example
        <svg class="contact-icon" viewBox="0 0 16 16"><rect x="1" y="3" width="14" height="10" rx="1" fill="var(--sun)"/><path d="M1.5 4l6.5 5 6.5-5" fill="none" stroke="var(--navy)" stroke-width="1.3"/></svg>
      </p>
      <p class="contact-row">www.velkpartners.example
        <svg class="contact-icon" viewBox="0 0 16 16"><circle cx="8" cy="8" r="7" fill="var(--sun)"/><path d="M1 8h14M8 1c-3 3.5-3 10.5 0 14M8 1c3 3.5 3 10.5 0 14" fill="none" stroke="var(--navy)" stroke-width="1"/></svg>
      </p>
    </div>
  </section>
</body>
</html>
```